Letter and Envelope Design For Harborline Realty

Please design a letter and an envelope incorporating our logo (See Attached). We are also launched a business card contest. Since we want them to match, please feel free to submit a design for both the business card and also the letter design and envelope.

Requirements
Must have
• The envelope, the letter and the business cards must match somehow connecting the designs. We want them to have something that holds them together besides the logo.

```html
<!DOCTYPE html>
<html lang="en">
<head>
<meta charset="utf-8">
<title>Harborline Realty Stationery</title>
<link href="https://fonts.googleapis.com/css2?family=Work+Sans:wght@400;500;600&display=swap" rel="stylesheet">
<style>
:root{
  --navy:#283180;
  --paper:#ffffff;
  --backdrop:#ebebeb;
  --ink:#5a5a5a;
  --ink-dark:#3f3f3f;
  --faint:#343d8c;
}
*{margin:0;padding:0;box-sizing:border-box}
html,body{width:1200px;height:762px;overflow:hidden;background:var(--backdrop)}
body{position:relative;font-family:"Work Sans",Arial,sans-serif;color:var(--ink)}
.sheet{position:absolute;background:var(--paper);overflow:hidden}
.band{position:absolute;left:0;top:0;width:100%;background:var(--navy)}
.seal{position:absolute;border-radius:50%;background:var(--paper);border:3px solid var(--navy)}
.brand-name{position:absolute;left:0;width:100%;text-align:center;color:var(--navy);font-weight:500;letter-spacing:.14em;white-space:nowrap}
.rule{position:absolute;height:1px;background:var(--navy)}
.contact{position:absolute;left:0;width:100%;text-align:center;color:var(--ink-dark);white-space:nowrap}
.contact b{color:var(--navy);font-weight:500}

/* letterhead */
.letterhead{left:45px;top:52px;width:466px;height:658px}
.letterhead .band{height:51px}
.letterhead .seal{left:209px;top:16px;width:68px;height:68px}
.letterhead .brand-name{top:138px;font-size:15px}
.salutation{position:absolute;left:33px;top:224px;font-size:13px;color:var(--navy)}
.letter-body{position:absolute;left:33px;top:258px;width:404px;font-size:9.2px;line-height:12px;color:var(--ink)}
.letter-body p{margin-bottom:12px}
.closing{position:absolute;left:33px;top:548px;font-size:10.5px;color:var(--ink-dark)}
.signature{position:absolute;left:33px;top:568px;width:84px;height:14px;background:linear-gradient(90deg,#d6d6dc,#ececf0)}
.letterhead .rule{left:33px;top:586px;width:400px}
.letterhead .contact{font-size:10.4px;padding-left:0}
.letterhead .contact.line1{top:606px}
.letterhead .contact.line2{top:623px}

/* card */
.card{left:549px;top:52px;width:606px;height:302px}
.card .band{height:66px}
.card .seal{left:259px;top:22px;width:88px;height:88px;border-width:4px}
.card .brand-name{top:162px;font-size:21px}
.card .rule{left:55px;top:229px;width:495px}
.card .contact{font-size:13px}
.card .contact.line1{top:247px}
.card .contact.line2{top:269px}

/* envelope */
.envelope{left:549px;top:408px;width:606px;height:302px;background:var(--navy)}
.envelope .flap{position:absolute;left:0;top:0}
.envelope .mark{position:absolute;left:273px;top:19px;width:54px;height:54px;border-radius:50%;border:2px solid var(--faint)}
.envelope .seal{left:273px;top:152px;width:60px;height:60px;background:transparent;border-color:var(--paper)}
.envelope .brand-name{top:221px;font-size:17px;color:var(--paper)}
</style>
</head>
<body>

<section class="sheet letterhead">
  <div class="band"></div>
  <div class="seal"></div>
  <div class="brand-name">HARBORLINE REALTY</div>
  <div class="salutation">Dear Sir</div>
  <div class="letter-body">
    <p>Lorem ipsum dolor sit amet, an vel recteque dissentiet, detracto albucius platonem ex vel, eros repudiandae cu. Atqui aliquando nec an, unum graece adolescens vel ad. Id odio scae has, iudico euismod atomorum ius ea, cum ea honestatis quaerendum theophrastus. Mea honestatis quaerendum theophrastus. Mea</p>
    <p>Lorem ipsum dolor sit amet, an vel recteque dissentiet, detracto albucius platonem ex vel, eros repudiandae cu. Atqui aliquando nec an, unum graece adolescens vel ad. Id odio scae has, iudico euismod atomorum ius ea, cum ea honestatis quaerendum theophrastus. Mea doming repudiandae ex, cu cum civibus assentior posidonium. Quo etiam pertinax ex, te eros repudiandae cu. Atqui aliquando nec an, unum graece adolescens vel ad. Id odio scae honestatis quaerendum theophrastus. Mea</p>
    <p>Lorem ipsum dolor sit amet, an vel recteque dissentiet, detracto albucius platonem ex vel, eros repudiandae cu. Atqui aliquando nec an, unum graece adolescens vel ad. Id odio scae has, iudico euismod atomorum ius ea, cum ea honestatis quaerendum theophrastus. Mea honestatis quaerendum theophrastus. Mea</p>
    <p>Lorem ipsum dolor sit amet, an vel recteque dissentiet, detracto albucius platonem ex vel, eros repudiandae cu. Atqui aliquando nec an, unum graece adolescens vel ad. Id odio scae has, iudico euismod atomorum ius ea, cum ea honestatis quaerendum theophrastus. Mea honestatis quaerendum theophrastus. Mea</p>
  </div>
  <div class="closing">Kind Regards</div>
  <div class="signature" role="img" aria-label="Handwritten signature"></div>
  <div class="rule"></div>
  <div class="contact line1"><b>P</b> : (555) 210-4870 | <b>E</b> : info@harborline.com | <b>W</b> : www.harborline.com</div>
  <div class="contact line2"><b>A</b> : 42 Quayside Lane, Port Avery, 7200</div>
</section>

<section class="sheet card">
  <div class="band"></div>
  <div class="seal"></div>
  <div class="brand-name">HARBORLINE REALTY</div>
  <div class="rule"></div>
  <div class="contact line1"><b>P</b> : (555) 210-4870 | <b>E</b> : info@harborline.com | <b>W</b> : www.harborline.com</div>
  <div class="contact line2"><b>A</b> : 42 Quayside Lane, Port Avery, 7200</div>
</section>

<section class="sheet envelope">
  <svg class="flap" width="606" height="302" viewBox="0 0 606 302" aria-hidden="true">
    <path d="M8 0 C12 40 14 70 42 88 Q52 94 70 94 L536 94 Q554 94 564 88 C592 70 594 40 598 0" fill="none" stroke="#1f2670" stroke-width="2"/>
  </svg>
  <div class="mark"></div>
  <div class="seal"></div>
  <div class="brand-name">HARBORLINE REALTY</div>
</section>

</body>
</html>
```